Business Cards for IT Consulting Company (Managed Service Provider)

I am looking to have some business cards printed and would like some designs. We are an IT Consulting company based in Vancouver BC. I would like a nice clean and modern look to the cards. I have uploaded all the versions of my logo so parts can be used as needed. Here is a snippit from our website homepage:

Quillbrook Networks Ltd. is an IT Solutions Partner located in Vancouver BC, Canada. We offer IT solutions and support to customers in the greater Vancouver Area. With expertise in Microsoft platforms, as well as Linux and Mac OSX and over 12 years experience in the IT industry, Quillbrook Networks is dedicated to offering our clients top quality service and products. We take pride in the solutions we offer our customers. The greatest compliment a client can give us is to recommend our services.

Quillbrook Networks Ltd. offers a wide range of IT services from onsite service to remote support and managed service solutions. This allows clients to choose the support path that best suits their company’s needs. Supporting many different sized companies from small to enterprise level over the past 12 years Quillbrook Networks has the experience and expertise needed to ensure things run smoothly. Allowing our clients to focus on doing business.

Revolutionizing the way IT services are delivered.

Quillbrook Networks is dedicated to providing our clients with IT solutions that work and grow with them for years to come. This philosophy helps save money in the long run instead of replacing equipment constantly. Far too often IT solutions are not well thought out and while possibly solving the problem at hand, require replacement due to growth or quality within a very short time frame. Quillbrook Networks takes pride in providing solutions that will last and be able to accommodate growth without the need for replacement.

Industry/Entity Type

Information Technology

Contact Information for Business Card

Quillbrook Networks Ltd.
(Employee Name)
Eml: (Employees Email Address)
Web: quillbrook.me
Ph: 604-555-0148

Font styles to use
Serif
Sans Serif

Requirements
Must have
• The Company logo and company colors.
Nice to have
• - Our tag line: "Revolutionizing IT Services" or "Revolutionizing the way IT services are delivered."
• - Also I really like the idea of nature and technology together blending which is sort of where my logo came from so integrating that somehow onto the business cards would be great.

```html
<!DOCTYPE html>
<html lang="en">
<head>
<meta charset="utf-8">
<title>Quillbrook Networks Ltd. – Business Card</title>
<link rel="stylesheet" href="https://fonts.googleapis.com/css2?family=Montserrat:wght@600;700&family=Open+Sans:wght@400&display=swap">
<style>
  :root {
    --page-bg: #dfe4ea;
    --card-light: #f1f3f6;
    --card-dark: #4b4c50;
    --card-dark-deep: #3e3f43;
    --brand-blue: #2f8fd8;
    --emblem-blue: rgba(30, 120, 210, 0.45);
    --name-blue: #3a86c8;
    --title-grey: #6b6f74;
    --text-grey: #6e7378;
    --icon-teal: #2e6f78;
  }
  * { margin: 0; padding: 0; box-sizing: border-box; }
  html, body { width: 1200px; height: 900px; overflow: hidden; }
  body { background: var(--page-bg); position: relative; }

  .business-card {
    position: absolute;
    left: 278px; top: 203px;
    width: 750px; height: 428px;
    display: flex;
    box-shadow: 0 10px 30px rgba(0,0,0,0.18);
  }
  .card-front {
    position: relative;
    width: 376px; height: 100%;
    background: var(--card-light);
  }
  .card-back {
    width: 374px; height: 100%;
    background:
      radial-gradient(ellipse 62% 55% at 68% 66%, var(--emblem-blue) 0%, rgba(30,120,210,0.12) 60%, rgba(30,120,210,0) 100%),
      linear-gradient(160deg, var(--card-dark) 0%, var(--card-dark-deep) 100%);
  }

  .brand-lockup {
    position: absolute;
    left: 32px; top: 42px;
    display: flex; align-items: center; gap: 14px;
    color: var(--brand-blue);
    font-family: "Montserrat", sans-serif;
    font-weight: 600;
  }
  .brand-mark { width: 40px; height: 40px; background: var(--brand-blue); }
  .brand-name { line-height: 1; }
  .brand-name .primary { display: block; font-size: 38px; letter-spacing: 0.2px; }
  .brand-name .secondary { display: block; font-size: 14px; letter-spacing: 0.6px; margin-top: 4px; }

  .person { position: absolute; left: 32px; top: 224px; font-family: "Montserrat", sans-serif; }
  .person-name { font-size: 24px; font-weight: 700; letter-spacing: 1.2px; color: var(--name-blue); }
  .person-title { font-size: 14px; font-weight: 700; color: var(--title-grey); margin-top: 6px; letter-spacing: 0.3px; }

  .contact-list {
    position: absolute; left: 32px; top: 296px;
    list-style: none;
    font-family: "Open Sans", sans-serif;
    font-size: 16px; color: var(--text-grey);
  }
  .contact-list li { display: flex; align-items: center; gap: 12px; height: 28px; }
  .contact-icon { width: 16px; height: 16px; flex: none; }
</style>
</head>
<body>
  <div class="business-card">
    <section class="card-front">
      <div class="brand-lockup">
        <span class="brand-mark"></span>
        <span class="brand-name">
          <span class="primary">quillbrook</span>
          <span class="secondary">NETWORKS LTD.</span>
        </span>
      </div>

      <div class="person">
        <p class="person-name">DANA WHITCOMBE</p>
        <p class="person-title">DIRECTOR</p>
      </div>

      <ul class="contact-list">
        <li>
          <svg class="contact-icon" viewBox="0 0 16 16" aria-hidden="true">
            <rect width="16" height="16" rx="2" fill="var(--icon-teal)"/>
            <path d="M4.5 3.5l2 .3.6 2.2-1.2.9a6 6 0 0 0 3.2 3.2l.9-1.2 2.2.6.3 2c-.3.6-1 .9-1.7.8A8 8 0 0 1 3.7 5.2c-.1-.7.2-1.4.8-1.7z" fill="#fff"/>
          </svg>
          <span>604-555-0148</span>
        </li>
        <li>
          <svg class="contact-icon" viewBox="0 0 16 16" aria-hidden="true">
            <rect width="16" height="16" rx="2" fill="var(--icon-teal)"/>
            <rect x="5" y="2.5" width="6" height="11" rx="1" fill="none" stroke="#fff" stroke-width="1.3"/>
            <circle cx="8" cy="11.4" r="0.7" fill="#fff"/>
          </svg>
          <span>604-555-0172</span>
        </li>
        <li>
          <svg class="contact-icon" viewBox="0 0 16 16" aria-hidden="true">
            <rect width="16" height="16" rx="2" fill="var(--icon-teal)"/>
            <rect x="3" y="4.5" width="10" height="7" fill="none" stroke="#fff" stroke-width="1.2"/>
            <path d="M3 4.5l5 4 5-4" fill="none" stroke="#fff" stroke-width="1.2"/>
          </svg>
          <span>danawhitcombe@quillbrook.me</span>
        </li>
        <li>
          <svg class="contact-icon" viewBox="0 0 16 16" aria-hidden="true">
            <rect width="16" height="16" rx="2" fill="var(--icon-teal)"/>
            <circle cx="8" cy="8" r="4.8" fill="none" stroke="#fff" stroke-width="1.1"/>
            <path d="M3.2 8h9.6M8 3.2c-2 2.6-2 7 0 9.6M8 3.2c2 2.6 2 7 0 9.6" fill="none" stroke="#fff" stroke-width="1"/>
          </svg>
          <span>quillbrook.me</span>
        </li>
      </ul>
    </section>

    <section class="card-back" role="img" aria-label="Dark panel where a large blue outlined brand emblem belongs"></section>
  </div>
</body>
</html>
```